KRV Business Card

Looking for a business card for my restaurant group I own. Four different concepts:

Copperfield Alehouse
Bristow Alehouse
Tanager's Stone Hearth Kitchen
Pellston Patty Company

Card doesn't need to include all the logos.

```html
<!DOCTYPE html>
<html lang="en">
<head>
<meta charset="utf-8">
<title>KRV Business Card</title>
<link rel="stylesheet" href="https://fonts.googleapis.com/css2?family=Josefin+Sans:wght@600;700&family=Lato:wght@400;700&display=swap">
<style>
  :root {
    --gold: #d2ad66;
    --gold-soft: #d8b673;
    --ink: #55555a;
    --white: #ffffff;
    --stage: #dcdcdc;
  }
  * { margin: 0; padding: 0; box-sizing: border-box; }
  html, body { width: 1200px; height: 802px; overflow: hidden; }
  body { background: var(--stage); position: relative; font-family: "Lato", sans-serif; }

  .card {
    position: absolute; top: 274px; width: 442px; height: 265px;
    box-shadow: 0 3px 6px rgba(0,0,0,0.25);
  }
  .card--front { left: 136px; background: var(--white); }
  .card--back { left: 625px; background: var(--gold); }

  .brand-mark {
    position: absolute; left: 0; width: 233px; top: 72px;
    text-align: center; color: var(--gold);
    font-family: "Josefin Sans", sans-serif; font-weight: 700;
    font-size: 44px; line-height: 1; letter-spacing: 2px;
  }
  .brand-name {
    position: absolute; left: 0; width: 233px; top: 138px; text-align: center;
    font-family: "Josefin Sans", sans-serif; font-weight: 600;
    color: var(--gold); font-size: 30px; letter-spacing: 3px; line-height: 1;
  }
  .brand-sub {
    position: absolute; left: 0; width: 233px; top: 176px; text-align: center;
    font-family: "Josefin Sans", sans-serif; font-weight: 600;
    font-size: 13.5px; letter-spacing: 2.2px; color: var(--ink); line-height: 1;
  }
  .brand-sub .accent { color: var(--gold); }

  .divider {
    position: absolute; left: 233px; top: 73px; width: 1px; height: 114px;
    background: #d9d9d9;
  }
  .contact { position: absolute; left: 251px; top: 72px; color: var(--ink); font-size: 12.5px; line-height: 1.3; }
  .contact__name { color: var(--gold); font-weight: 700; font-size: 16px; letter-spacing: 0.3px; line-height: 1; }
  .contact__role { margin-bottom: 5px; }
  .contact__row { display: flex; align-items: center; gap: 4px; height: 17px; }
  .contact__row svg { width: 10px; height: 10px; fill: var(--gold); }
  .contact__address { margin-top: 7px; line-height: 1.3; }

  .back-pattern { position: absolute; inset: 0; background: var(--gold-soft); }
  .back-name {
    position: absolute; left: 0; right: 0; top: 99px; text-align: center;
    font-family: "Josefin Sans", sans-serif; font-weight: 600;
    color: var(--white); font-size: 42px; letter-spacing: 4px; line-height: 1;
  }
  .back-sub {
    position: absolute; left: 0; right: 0; top: 147px; text-align: center;
    font-family: "Josefin Sans", sans-serif; font-weight: 600;
    color: var(--white); font-size: 18px; letter-spacing: 2.6px; line-height: 1;
  }
  .concepts {
    position: absolute; left: 0; right: 0; top: 216px; text-align: center;
    color: var(--white); font-weight: 700; font-size: 10.5px; line-height: 14px;
    text-transform: uppercase; letter-spacing: -0.1px;
  }
</style>
</head>
<body>
  <section class="card card--front">
    <div class="brand-mark">KRV</div>
    <div class="brand-name">KESTREL</div>
    <div class="brand-sub">HOSPITALITY <span class="accent">GROUP</span></div>
    <div class="divider"></div>
    <div class="contact">
      <div class="contact__name">DANIEL HARTLEY</div>
      <div class="contact__role">Managing Director</div>
      <div class="contact__row"><svg viewBox="0 0 10 10"><path d="M1 3c0-1 1-2 4-2s4 1 4 2v1H7V3H3v1H1z M2 5h6l1 4H1z"/></svg>044-555 218 730</div>
      <div class="contact__row"><svg viewBox="0 0 10 10"><path d="M0 2h10v6H0z" /><path d="M0 2l5 3 5-3" fill="none" stroke="#fff" stroke-width="1"/></svg>info@webname.com</div>
      <div class="contact__row"><svg viewBox="0 0 10 10"><circle cx="5" cy="5" r="4.5"/></svg>www.websitename.com</div>
      <div class="contact__address">421, Address line here<br>Country Name, 45452</div>
    </div>
  </section>

  <section class="card card--back">
    <div class="back-pattern" role="img" aria-label="Faint repeating monogram pattern on gold"></div>
    <div class="back-name">KESTREL</div>
    <div class="back-sub">HOSPITALITY GROUP</div>
    <div class="concepts">
      Copperfield Alehouse &nbsp;|&nbsp; Bristow Alehouse<br>
      Tanager's Stone Hearth Kitchen &nbsp;|&nbsp; Pellston Patty Company
    </div>
  </section>
</body>
</html>
```